Request for Business Card Design

Hi. My name is Marlene, I am looking for a new business card design for my company, Quarrow Signal Instruments, LLC. I really like the design you did for Tarsel Venture and was hoping you could do something similar using our full logo and our mark. I am also open to any raised texture design using our mark. I have attached our full logo, which would need to be somewhere on the card, as well as the mark in both outline and full form, as well as our brand colors / guide. The card does not have to be white, as long as our logo and mark appear. I actually like darker colored business cards more, but am open to all options. If you are interested in working with me, please let me know. We would also take the business card design into letterhead design if you can do that.

```html
<!DOCTYPE html>
<html lang="en">
<head>
<meta charset="utf-8">
<title>Quarrow Signal Instruments – Business Card</title>
<link rel="stylesheet" href="https://fonts.googleapis.com/css2?family=Arimo:wght@400;700&display=swap">
<style>
  :root {
    --stage: #0c0c0d;
    --card: #232325;
    --card-back: #1d1d1f;
    --pattern: #2a2a2c;
    --accent: #0095c0;
    --ink: #ffffff;
  }
  * { margin: 0; padding: 0; box-sizing: border-box; }
  html, body {
    width: 1200px; height: 963px; overflow: hidden;
    background: var(--stage);
    font-family: "Arimo", Arial, sans-serif;
  }
  .stage {
    width: 1200px; height: 963px;
    display: flex; flex-direction: column; align-items: center; justify-content: center; gap: 40px;
  }
  .card {
    position: relative; width: 700px; height: 400px;
    border-radius: 24px; overflow: hidden;
    background: var(--card);
    box-shadow: 0 6px 0 var(--accent), 0 16px 30px rgba(0,0,0,.6);
  }
  /* Front */
  .holder { position: absolute; left: 48px; top: 62px; }
  .holder-name {
    color: var(--accent); font-weight: 700; font-size: 22px; letter-spacing: .5px;
    text-transform: uppercase; white-space: nowrap;
  }
  .holder-role { color: var(--ink); font-size: 16px; margin-top: 4px; }
  .divider {
    position: absolute; left: 48px; right: 48px; top: 138px; height: 1.5px; background: var(--accent);
  }
  .contacts { position: absolute; left: 48px; top: 164px; list-style: none; }
  .contacts li {
    display: flex; align-items: center; gap: 12px;
    color: var(--ink); font-size: 17px; line-height: 32px; white-space: nowrap;
  }
  .contacts svg { width: 16px; height: 16px; flex: none; }
  .brand { position: absolute; right: 48px; top: 52px; display: flex; align-items: center; gap: 14px; }
  .brand-dot { width: 54px; height: 54px; border-radius: 50%; background: var(--accent); flex: none; }
  .brand-text { color: var(--ink); font-weight: 700; text-transform: uppercase; white-space: nowrap; }
  .brand-name { font-size: 32px; letter-spacing: 3px; line-height: 1; }
  .brand-sub { font-size: 11px; letter-spacing: 1.2px; margin-top: 6px; }
  .address {
    position: absolute; right: 48px; bottom: 46px; text-align: right;
    color: var(--ink); font-size: 17px; line-height: 26px; white-space: nowrap;
  }
  /* Back */
  .card-back { background: var(--card-back); }
  .raised-pattern {
    position: absolute; inset: 0;
    background: linear-gradient(135deg, var(--pattern) 0%, #1a1a1c 55%, #2d2d30 100%);
  }
  .back-brand { position: absolute; right: 60px; bottom: 60px; display: flex; align-items: center; gap: 12px; }
  .back-brand .brand-dot { width: 40px; height: 40px; }
  .back-brand .brand-name { color: var(--accent); font-weight: 700; font-size: 20px; letter-spacing: 2px; text-transform: uppercase; }
</style>
</head>
<body>
<main class="stage">
  <section class="card card-front">
    <div class="holder">
      <p class="holder-name">Marlene Hadley</p>
      <p class="holder-role">Manager</p>
    </div>
    <div class="brand">
      <span class="brand-dot"></span>
      <div class="brand-text">
        <p class="brand-name">Quarrow</p>
        <p class="brand-sub">Signal Instruments</p>
      </div>
    </div>
    <div class="divider"></div>
    <ul class="contacts">
      <li>
        <svg viewBox="0 0 16 16" fill="none" stroke="var(--accent)" stroke-width="1.6"><path d="M4 1.5l2 3-1.5 1.5a8 8 0 0 0 5.5 5.5L11.5 10l3 2-1.5 2.5C7 14.5 1.5 9 1.5 3z"/></svg>
        555-014-7720
      </li>
      <li>
        <svg viewBox="0 0 16 16" fill="none" stroke="var(--accent)" stroke-width="1.4"><rect x="1.5" y="3.5" width="13" height="9" rx="1"/><path d="M1.5 4l6.5 5 6.5-5"/></svg>
        marlene@quarrowsignal.com
      </li>
      <li>
        <svg viewBox="0 0 16 16" fill="none" stroke="var(--accent)" stroke-width="1.3"><circle cx="8" cy="8" r="6.5"/><path d="M1.5 8h13M8 1.5c-3 3.5-3 9.5 0 13M8 1.5c3 3.5 3 9.5 0 13"/></svg>
        www.quarrowsignal.com
      </li>
    </ul>
    <p class="address">48 Lantern Row, Eastvale<br>Colorado, 80112</p>
  </section>

  <section class="card card-back">
    <div class="raised-pattern" role="img" aria-label="Raised tone-on-tone repeating pattern of the company mark across the card back"></div>
    <div class="back-brand">
      <span class="brand-dot"></span>
      <p class="brand-name">Quarrow</p>
    </div>
  </section>
</main>
</body>
</html>
```